Vento Hallmark Real estate Costa del sol

we need a website for our Company based in Costa del sol, Spain. We sell properties on the spanish coast that is called costa del sol. We are concentrating on exclusive properties and would like the webdesign to show this. In our website we want to have area descriptions of the different areas we sell our Products. We will also implement a searchable database delivered by a third part where all properties for sale in Spain are listed. When looking into the designs we would like our main page to have a overview of the coast where the different areas are shown. Have a look at brightlunavista.example or oakterra.example to see. The webpage will be presented in 4 languages, English, spanish, Swedish and norwegian, and shall of course also be prepared for social medias. We want an easy Contemporary design but still with an exclusive feeling!
Scandinavian and North european Citizens wants to buy a property in Spain
Real Estate
5+ page

```html
<!DOCTYPE html>
<html lang="en">
<head>
<meta charset="utf-8">
<title>Vento Hallmark – Real Estate Costa del Sol</title>
<link rel="stylesheet" href="https://fonts.googleapis.com/css2?family=Noto+Serif:wght@400;700&family=Open+Sans:wght@400;600;700&display=swap">
<style>
:root{
  --navy:#1c2152;
  --ink:#222;
  --dark:#1f1f1f;
  --darker:#171717;
  --panel:#2a2a2a;
  --tab:#5b5b5b;
  --muted:#777;
  --light:#f3f3f3;
  --line:#d9d9d9;
  --white:#fff;
  --serif:'Noto Serif', Georgia, serif;
  --sans:'Open Sans', Arial, sans-serif;
}
*{box-sizing:border-box;margin:0;padding:0}
html,body{width:1200px;height:2970px;overflow:hidden}
body{position:relative;font-family:var(--sans);color:var(--ink);background:var(--white)}
.abs{position:absolute}
svg{display:block}

/* header */
.topbar{left:605px;top:0;width:595px;height:32px;background:var(--darker);display:flex;align-items:center;color:#ddd;font-size:13px}
.topbar .soc{width:30px;height:32px;display:flex;align-items:center;justify-content:center;border-right:1px solid #333}
.topbar .soc span{width:10px;height:10px;background:#bbb;display:block}
.topbar .soc.on{background:#555}
.topbar .lang{display:flex;align-items:center;gap:6px;padding:0 18px;border-right:1px solid #333;height:32px;font-size:11px}
.topbar .lang i{width:14px;height:9px;background:#6b7bb0;display:block}
.topbar .call{display:flex;align-items:center;gap:8px;padding-left:16px;font-size:14px}
.header{left:0;top:32px;width:1200px;height:71px;background:rgba(245,245,245,.95);z-index:2}
.brand{left:162px;top:10px;width:150px;height:86px;z-index:3;display:flex;flex-direction:column;align-items:center}
.brand .mark{width:40px;height:40px;border:4px solid var(--ink)}
.brand .name{font-family:var(--serif);font-size:19px;color:var(--ink);margin-top:6px;white-space:nowrap}
.nav{left:440px;top:56px;display:flex;gap:0;z-index:3;font-size:14px}
.nav a{color:var(--ink);text-decoration:none;padding:0 14px}
.nav a.active{font-weight:700;border-bottom:2px solid var(--navy);padding-bottom:6px}

/* hero */
.hero{left:0;top:103px;width:1200px;height:495px;background:linear-gradient(180deg,#6f7f8d 0%,#8f9598 40%,#5a5650 75%,#3b3a33 100%)}
.hero-copy{left:246px;top:290px;color:var(--white)}
.hero-copy .kicker{font-size:15px;font-weight:600;letter-spacing:.3px}
.hero-copy h1{font-family:var(--serif);font-size:26px;line-height:30px;font-weight:700;margin-top:8px}
.btn-navy{display:inline-block;background:var(--navy);color:var(--white);font-size:13px;border:1px solid #8a8fb0;padding:9px 27px;margin-top:18px}
.hero-arrow{top:322px}
.dots{display:flex;gap:8px;align-items:center}
.dots i{width:10px;height:10px;border-radius:50%;background:#fff;display:block}
.dots i.on{width:14px;height:14px;background:transparent;border:2px solid #fff;box-shadow:inset 0 0 0 2px var(--navy)}

/* search */
.search{left:0;top:598px;width:1200px;height:260px;background:var(--panel)}
.tab{top:598px;height:45px;display:flex;align-items:center;gap:12px;font-family:var(--serif);font-size:17px;color:var(--white);padding-left:26px}
.tab.one{left:317px;width:202px;background:var(--tab)}
.tab.two{left:519px;width:176px;background:#1d1d1d}
.discover{left:164px;top:686px;color:var(--white)}
.discover p{font-size:14px;letter-spacing:.3px}
.discover h2{font-family:var(--serif);font-weight:400;font-size:33px;line-height:40px;margin-top:4px}
.select{height:36px;border:1px solid #4a4a4a;background:#222;color:#ddd;font-size:11px;display:flex;align-items:center;justify-content:space-between;padding:0 14px}
.select::after{content:"";width:6px;height:6px;border-right:1.5px solid #ccc;border-bottom:1.5px solid #ccc;transform:rotate(45deg);margin-top:-4px}
.range{font-size:11px;color:#ddd}
.range .track{position:relative;width:218px;height:2px;background:#666;margin-top:16px}
.range .track b{position:absolute;top:0;height:2px;background:#fff}
.range .track i{position:absolute;top:-6px;width:13px;height:13px;border-radius:50%;background:#fff}
.btn-search{left:822px;top:794px;width:216px;height:32px;background:var(--white);display:flex;align-items:center;justify-content:center;gap:8px;font-size:12px;color:var(--ink)}

/* section titles */
.sec-title{display:flex;align-items:center;gap:14px;font-family:var(--serif);font-size:24px;color:var(--ink);letter-spacing:.5px}
.sec-title .sq{width:28px;height:28px;border:3px solid var(--ink)}
.rule{height:3px;background:var(--navy)}

/* developments */
.devs{left:0;top:858px;width:1200px;height:429px;background:var(--light)}
.pager{display:flex;gap:2px}
.pager span{width:24px;height:24px;background:#ddd;display:flex;align-items:center;justify-content:center}
.pager span.on{background:var(--navy)}
.viewall{left:962px;top:905px;width:76px;height:24px;background:var(--navy);color:#fff;font-size:11px;display:flex;align-items:center;justify-content:center}
.card{top:958px;width:218px;height:284px;background:var(--white)}
.card .ph{position:absolute;left:14px;top:12px;width:192px;height:121px}
.card .sale{position:absolute;left:14px;top:12px;background:var(--navy);color:#fff;font-size:10px;padding:3px 10px}
.card h3{position:absolute;left:14px;top:146px;font-size:12px;font-weight:600}
.card .meta{position:absolute;left:14px;top:170px;width:192px;display:flex;justify-content:space-between;font-size:11px;font-weight:600}
.card .meta em{font-style:normal;font-weight:400;display:flex;gap:5px;align-items:center;color:#444}
.card p{position:absolute;left:14px;top:193px;width:192px;font-size:10px;line-height:13px;color:#777}
.card .stats{position:absolute;left:0;bottom:0;width:218px;height:26px;background:var(--navy);display:flex;align-items:center;justify-content:space-around;color:#fff;font-size:9px}
.card .stats span{display:flex;gap:4px;align-items:center}
.card .stats i{width:9px;height:8px;border:1px solid #fff;display:block}
.hover{position:absolute;left:14px;top:12px;width:192px;height:121px;display:flex;flex-direction:column;align-items:center;justify-content:center;gap:8px}
.hover .tip{background:#333;color:#eee;font-size:9px;padding:2px 8px}
.hover .row{display:flex;gap:8px}
.hover .row i{width:22px;height:22px;border-radius:50%;border:1px solid #ccc;display:block}

/* promoted */
.promo-kicker{left:0;top:1330px;width:1200px;text-align:center;font-size:12px;color:#444}
.tile{color:#fff}
.tile .cap{position:absolute;left:0;bottom:0;width:100%;padding:0 18px 14px;background:linear-gradient(180deg,rgba(0,0,0,0),rgba(0,0,0,.55));display:flex;justify-content:space-between;align-items:flex-end}
.tile h4{font-family:var(--serif);font-weight:400;font-size:20px}
.tile.sm h4{font-size:14px}
.tile small{font-size:11px;color:#ddd;display:block;margin-top:2px}
.tile .price{text-align:right;font-size:11px}
.tile .price b{font-family:var(--serif);font-weight:400;font-size:19px;margin-left:6px}
.tile.sm .price b{font-size:14px}
.tile .price span{display:flex;gap:5px;justify-content:flex-end;align-items:center;margin-top:4px}
.gdots i{background:#bbb;width:10px;height:10px}
.gdots i.on{background:#555;width:10px;height:10px;border:0;box-shadow:none}

/* testimonials */
.testi{left:0;top:1934px;width:1200px;height:359px;background:linear-gradient(180deg,#2a2a2c,#1b1c20 60%,#26272b)}
.face{left:160px;width:52px;height:52px;background:linear-gradient(180deg,#c9c9c9,#8a8a8a)}
.quotebox{left:259px;top:2075px;width:779px;height:172px;border:1px solid #555;color:#fff;text-align:center}
.quotebox p{position:absolute;left:60px;top:50px;width:660px;font-size:11.5px;line-height:18px;color:#eee}
.quotebox b{position:absolute;left:0;top:136px;width:100%;font-family:var(--serif);font-size:12px}

/* clients */
.clients-desc{left:260px;top:2406px;width:680px;text-align:center;font-size:11.5px;line-height:18px;color:#444}
.logo-box{top:2455px;width:115px;height:80px;border:1px solid var(--line);display:flex;align-items:center;justify-content:center;font-size:16px;font-weight:700;color:#333}

/* footer */
.foot-l{left:0;top:2628px;width:483px;height:299px;background:var(--darker)}
.foot-r{left:483px;top:2628px;width:717px;height:299px;background:#232323}
.foot-mark{left:164px;top:2672px;width:50px;height:50px;border:5px solid #ddd}
.foot-about{left:164px;top:2742px;width:290px;font-size:12px;line-height:20px;color:#ddd}
.fsoc{top:2852px;width:24px;height:24px;background:#2f2f2f;display:flex;align-items:center;justify-content:center}
.fsoc span{width:9px;height:9px;background:#bbb;display:block}
.fsoc.on{background:#fff}
.fsoc.on span{background:#222}
.foot h5{font-family:var(--serif);font-weight:400;font-size:17px;color:#fff}
.contact-row{left:529px;display:flex;gap:16px;color:#ccc;font-size:11px;line-height:17px}
.contact-row strong{color:#fff;font-size:11px}
.cities{font-size:11px;color:#ccc;line-height:22.6px}
.cities li{list-style:none;display:flex;align-items:center;gap:10px}
.cities li::before{content:"";width:4px;height:4px;border-right:1px solid #aaa;border-top:1px solid #aaa;transform:rotate(45deg)}
.bottom{left:0;top:2927px;width:1200px;height:43px;background:var(--white);font-size:12px;color:#333}
.bottom .copy{position:absolute;left:164px;top:14px}
.bottom nav{position:absolute;right:162px;top:14px;display:flex;gap:22px}
.bottom nav a{color:#333;text-decoration:none}
.bottom nav a.active{font-weight:700}
</style>
</head>
<body>

<!-- header -->
<div class="abs header"></div>
<div class="abs topbar">
  <div class="soc" aria-label="Social network"><span></span></div>
  <div class="soc on" aria-label="Social network"><span></span></div>
  <div class="soc" aria-label="Social network"><span></span></div>
  <div class="soc" aria-label="Social network"><span></span></div>
  <div class="soc" aria-label="Social network"><span></span></div>
  <div class="lang"><i></i>English
    <svg width="8" height="6" viewBox="0 0 8 6"><path d="M1 1l3 3 3-3" stroke="#ccc" fill="none"/></svg></div>
  <div class="call">
    <svg width="13" height="13" viewBox="0 0 24 24"><path fill="#ddd" d="M6.6 10.8a15 15 0 006.6 6.6l2.2-2.2a1 1 0 011-.25 11.4 11.4 0 003.6.57 1 1 0 011 1V20a1 1 0 01-1 1A17 17 0 013 4a1 1 0 011-1h3.5a1 1 0 011 1c0 1.25.2 2.45.57 3.57a1 1 0 01-.25 1z"/></svg>
    Call : 0987 654 321</div>
</div>
<div class="abs brand"><div class="mark"></div><div class="name">Vento Hallmark</div></div>
<nav class="abs nav">
  <a class="active" href="#">Home</a><a href="#">About Us</a><a href="#">Costa del Sol</a><a href="#">Services</a><a href="#">Testimonials</a><a href="#">Contact Us</a>
</nav>

<!-- hero -->
<div class="abs hero" role="img" aria-label="Photograph of a large two-storey family house with stone garage among pine trees"></div>
<div class="abs hero-copy">
  <div class="kicker">WE CREATE VALUE TO YOUR LIVES</div>
  <h1>We Are Always Here To<br>Fullfil Your Dreams</h1>
  <span class="btn-navy">Read More</span>
</div>
<svg class="abs hero-arrow" style="left:66px" width="36" height="60" viewBox="0 0 36 60"><path d="M30 4L6 30l24 26" stroke="#fff" stroke-width="2" fill="none" opacity=".8"/></svg>
<svg class="abs hero-arrow" style="left:1096px" width="36" height="60" viewBox="0 0 36 60"><path d="M6 4l24 26L6 56" stroke="#fff" stroke-width="2" fill="none" opacity=".8"/></svg>
<div class="abs dots" style="left:570px;top:559px"><i></i><i class="on"></i><i></i></div>

<!-- search -->
<div class="abs search"></div>
<div class="abs tab one">
  <svg width="15" height="15" viewBox="0 0 16 16"><circle cx="6.5" cy="6.5" r="4.5" stroke="#fff" stroke-width="2" fill="none"/><path d="M10 10l4.5 4.5" stroke="#fff" stroke-width="2"/></svg>Find Your Home</div>
<div class="abs tab two">
  <svg width="15" height="14" viewBox="0 0 16 14"><path d="M8 1L1 7h2v6h4V9h2v4h4V7h2z" fill="#fff"/></svg>House for sell</div>
<div class="abs discover"><p>DISCOVER YOUR</p><h2>DREAM<br>HOUSE</h2></div>
<div class="abs select" style="left:348px;top:677px;width:218px">Location</div>
<div class="abs select" style="left:584px;top:677px;width:218px">Sub-location</div>
<div class="abs select" style="left:822px;top:677px;width:216px">Status</div>
<div class="abs select" style="left:348px;top:735px;width:218px">No.of Bedrooms</div>
<div class="abs select" style="left:584px;top:735px;width:218px">No.of Bathrooms</div>
<div class="abs select" style="left:822px;top:735px;width:216px">No.of Guest</div>
<div class="abs range" style="left:350px;top:788px">No.of Bedrooms
  <div class="track"><b style="left:6px;width:110px"></b><i style="left:0"></i><i style="left:110px"></i></div></div>
<div class="abs range" style="left:586px;top:788px">Area [150 - 720]
  <div class="track"><b style="left:52px;width:110px"></b><i style="left:46px"></i><i style="left:156px"></i></div></div>
<div class="abs btn-search">
  <svg width="12" height="12" viewBox="0 0 16 16"><circle cx="6.5" cy="6.5" r="4.5" stroke="#222" stroke-width="2" fill="none"/><path d="M10 10l4.5 4.5" stroke="#222" stroke-width="2"/></svg>Search Property</div>

<!-- new developments -->
<section class="abs devs"></section>
<div class="abs sec-title" style="left:162px;top:900px"><span class="sq"></span>NEW DEVELOPMENTS</div>
<div class="abs rule" style="left:162px;top:947px;width:100px"></div>
<div class="abs pager" style="left:896px;top:905px">
  <span><svg width="6" height="9" viewBox="0 0 6 9"><path d="M5 1L1 4.5 5 8" stroke="#555" fill="none"/></svg></span>
  <span style="background:#aaa"><svg width="6" height="9" viewBox="0 0 6 9"><path d="M1 1l4 3.5L1 8" stroke="#fff" fill="none"/></svg></span>
</div>
<div class="abs viewall">View All</div>

<div class="abs card" style="left:162px">
  <div class="ph" role="img" aria-label="Photograph of a modern villa lit at dusk" style="background:linear-gradient(180deg,#3b3f4e,#6a4a2e)"></div>
  <h3>EL Rehab Mountain Vills</h3>
  <div class="meta">$ 125.000<em><svg width="8" height="11" viewBox="0 0 8 11"><path d="M4 0a4 4 0 00-4 4c0 3 4 7 4 7s4-4 4-7a4 4 0 00-4-4z" fill="#444"/></svg>Miami, USA</em></div>
  <p>Lorem ipsum dolor sit amet, consec tet uer adipiscing elit, sed diam nonu mmy nibh euismod tincidunt ut laoreet.</p>
  <div class="stats"><span><i></i>330 m2</span><span><i></i>8</span><span><i></i>3</span><span><i></i>2</span></div>
</div>
<div class="abs card" style="left:382px">
  <div class="ph" role="img" aria-label="Photograph of a contemporary house at night" style="background:linear-gradient(180deg,#2b2b31,#4a3f36)"></div>
  <div class="hover"><span class="tip">Add To Favourite</span><div class="row"><i></i><i style="background:#fff"></i><i></i></div></div>
  <h3>EL Rehab Mountain Vills</h3>
  <div class="meta">$ 125.000<em><svg width="8" height="11" viewBox="0 0 8 11"><path d="M4 0a4 4 0 00-4 4c0 3 4 7 4 7s4-4 4-7a4 4 0 00-4-4z" fill="#444"/></svg>Miami, USA</em></div>
  <p>Lorem ipsum dolor sit amet, consec tet uer adipiscing elit, sed diam nonu mmy nibh euismod tincidunt ut laoreet.</p>
  <div class="stats"><span><i></i>330 m2</span><span><i></i>8</span><span><i></i>3</span><span><i></i>2</span></div>
</div>
<div class="abs card" style="left:602px">
  <div class="ph" role="img" aria-label="Photograph of a single-storey house with a lawn under blue sky" style="background:linear-gradient(180deg,#5f86b8,#8c9a9b 55%,#5d7a45)"></div>
  <span class="sale">Sale</span>
  <h3>EL Rehab Mountain Vills</h3>
  <div class="meta">$ 125.000<em><svg width="8" height="11" viewBox="0 0 8 11"><path d="M4 0a4 4 0 00-4 4c0 3 4 7 4 7s4-4 4-7a4 4 0 00-4-4z" fill="#444"/></svg>Miami, USA</em></div>
  <p>Lorem ipsum dolor sit amet, consec tet uer adipiscing elit, sed diam nonu mmy nibh euismod tincidunt ut laoreet.</p>
  <div class="stats"><span><i></i>330 m2</span><span><i></i>8</span><span><i></i>3</span><span><i></i>2</span></div>
</div>
<div class="abs card" style="left:822px">
  <div class="ph" role="img" aria-label="Photograph of a Mediterranean villa with palm trees" style="background:linear-gradient(180deg,#6fa0d4,#c49a6a 60%,#6b7d3e)"></div>
  <span class="sale">Sale</span>
  <h3>EL Rehab Mountain Vills</h3>
  <div class="meta">$ 125.000<em><svg width="8" height="11" viewBox="0 0 8 11"><path d="M4 0a4 4 0 00-4 4c0 3 4 7 4 7s4-4 4-7a4 4 0 00-4-4z" fill="#444"/></svg>Miami, USA</em></div>
  <p>Lorem ipsum dolor sit amet, consec tet uer adipiscing elit, sed diam nonu mmy nibh euismod tincidunt ut laoreet.</p>
  <div class="stats"><span><i></i>330 m2</span><span><i></i>8</span><span><i></i>3</span><span><i></i>2</span></div>
</div>

<!-- specially promoted -->
<div class="abs promo-kicker">Find Property in YOur City</div>
<div class="abs sec-title" style="left:0;top:1350px;width:1200px;justify-content:center"><span class="sq"></span>SPECIALLY PROMOTED</div>
<div class="abs rule" style="left:562px;top:1396px;width:76px"></div>

<div class="abs tile" style="left:162px;top:1420px;width:426px;height:427px;background:linear-gradient(180deg,#a87aa8,#c99bb7 35%,#6d6a6a 65%,#4f6b3a)" role="img" aria-label="Photograph of a suburban villa with lit windows at pink sunset">
  <div class="cap"><div><h4>Laxury Villa</h4><small>33 Properties</small></div>
  <div class="price">Start From <b>$152.000</b><span><svg width="8" height="11" viewBox="0 0 8 11"><path d="M4 0a4 4 0 00-4 4c0 3 4 7 4 7s4-4 4-7a4 4 0 00-4-4z" fill="#fff"/></svg>Miami, USA</span></div></div>
</div>
<div class="abs tile" style="left:612px;top:1420px;width:426px;height:202px;background:linear-gradient(180deg,#2a3a6a,#3a3550 45%,#7a5a35 70%,#1e3b5a)" role="img" aria-label="Photograph of a villa with an illuminated swimming pool at night">
  <div class="cap"><div><h4>Swimming Pool</h4><small>52 Properties</small></div>
  <div class="price">Start From <b>$143.000</b><span><svg width="8" height="11" viewBox="0 0 8 11"><path d="M4 0a4 4 0 00-4 4c0 3 4 7 4 7s4-4 4-7a4 4 0 00-4-4z" fill="#fff"/></svg>Hawai</span></div></div>
</div>
<div class="abs tile sm" style="left:612px;top:1645px;width:200px;height:202px;background:linear-gradient(180deg,#4f7fb9,#7a5f52 50%,#4f5d3c)" role="img" aria-label="Photograph of a cosy brick house with gables">
  <div class="cap" style="padding:0 12px 12px"><div><h4>Cozy houses</h4><small>19 Properties</small></div>
  <div class="price"><b>$22.000</b><span><svg width="8" height="11" viewBox="0 0 8 11"><path d="M4 0a4 4 0 00-4 4c0 3 4 7 4 7s4-4 4-7a4 4 0 00-4-4z" fill="#fff"/></svg>Maine</span></div></div>
</div>
<div class="abs tile sm" style="left:837px;top:1645px;width:201px;height:202px;background:linear-gradient(180deg,#8aa4c4,#9a9a98 50%,#4e5346)" role="img" aria-label="Photograph of a grey family house with gardens">
  <div class="cap" style="padding:0 12px 12px"><div><h4>Gardens</h4><small>88 Properties</small></div>
  <div class="price"><b>$24.000</b><span><svg width="8" height="11" viewBox="0 0 8 11"><path d="M4 0a4 4 0 00-4 4c0 3 4 7 4 7s4-4 4-7a4 4 0 00-4-4z" fill="#fff"/></svg>Miami</span></div></div>
</div>
<div class="abs dots gdots" style="left:572px;top:1878px"><i></i><i class="on"></i><i></i><i></i></div>

<!-- testimonials -->
<section class="abs testi" role="img" aria-label="Dimmed photograph of a house at night behind the testimonials"></section>
<div class="abs sec-title" style="left:0;top:1976px;width:1200px;justify-content:center;color:#fff"><span class="sq" style="border-color:#fff"></span>CLIENTS TESTIMONIALS</div>
<div class="abs rule" style="left:562px;top:2024px;width:76px;background:#fff"></div>
<div class="abs face" style="top:2077px" role="img" aria-label="Portrait of a client"></div>
<div class="abs face" style="top:2136px" role="img" aria-label="Portrait of a client"></div>
<div class="abs face" style="top:2196px" role="img" aria-label="Portrait of a client"></div>
<svg class="abs" style="left:212px;top:2100px" width="48" height="6" viewBox="0 0 48 6"><path d="M0 3h46" stroke="#ccc"/><circle cx="45" cy="3" r="2.5" fill="#fff"/></svg>
<div class="abs quotebox">
  <svg style="position:absolute;left:370px;top:-6px" width="40" height="34" viewBox="0 0 40 34"><rect x="0" y="0" width="40" height="34" fill="#222"/><path d="M4 30V18C4 8 9 4 16 3v5c-4 1-6 4-6 8h6v14zM22 30V18c0-10 5-14 12-15v5c-4 1-6 4-6 8h6v14z" fill="#fff"/></svg>
  <p>Lorem Ipsum is simply dummy text of the printing and typesetting industry. Lorem Ipsum has been the industry's standard dummy text ever since the 1500s, when an unknown printer took a galley of type and scrambled it to make a type specimen book. It has survived not only five centuries, but mmy text ever since the 1500s, when an unknown printer took a galley of type and scramblalso the leap into electronic typesetting, remaining essentiall.</p>
  <b>- Mr. John Doe, Company Name</b>
</div>
<svg class="abs" style="left:124px;top:2146px" width="14" height="26" viewBox="0 0 14 26"><path d="M12 2L2 13l10 11" stroke="#aaa" fill="none" stroke-width="1.5"/></svg>
<svg class="abs" style="left:1062px;top:2146px" width="14" height="26" viewBox="0 0 14 26"><path d="M2 2l10 11L2 24" stroke="#aaa" fill="none" stroke-width="1.5"/></svg>

<!-- valued clients -->
<div class="abs sec-title" style="left:0;top:2336px;width:1200px;justify-content:center"><span class="sq"></span>OUR VALUED CLIENTS</div>
<div class="abs clients-desc">Lorem Ipsum is simply dummy text of the printing and typesetting industry. Lorem Ipsum has been the industry's standard dummy text ever since the 1500s, when an unknown.</div>
<div class="abs logo-box" style="left:162px">Norvik</div>
<div class="abs logo-box" style="left:289px">Kestrel Labs</div>
<div class="abs logo-box" style="left:416px">Brightfield</div>
<div class="abs logo-box" style="left:543px">Ledgerly</div>
<div class="abs logo-box" style="left:670px">Portico</div>
<div class="abs logo-box" style="left:797px">Lumen Grid</div>
<div class="abs logo-box" style="left:924px">Kestrel Labs</div>
<div class="abs pager" style="left:574px;top:2556px">
  <span><svg width="6" height="9" viewBox="0 0 6 9"><path d="M5 1L1 4.5 5 8" stroke="#555" fill="none"/></svg></span>
  <span class="on"><svg width="6" height="9" viewBox="0 0 6 9"><path d="M1 1l4 3.5L1 8" stroke="#fff" fill="none"/></svg></span>
</div>

<!-- footer -->
<footer class="foot">
  <div class="abs foot-l"></div>
  <div class="abs foot-r"></div>
  <div class="abs foot-mark"></div>
  <p class="abs foot-about">Lorem Ipsum is simply dummy text of the printing and typesetting industry. Lorem Ipsum has been the industry's standard dummy text ever since the 1500s, when an unknown prik a galley.</p>
  <div class="abs fsoc" style="left:164px"><span></span></div>
  <div class="abs fsoc" style="left:196px"><span></span></div>
  <div class="abs fsoc on" style="left:228px"><span></span></div>
  <div class="abs fsoc" style="left:260px"><span></span></div>
  <div class="abs fsoc" style="left:292px"><span></span></div>

  <h5 class="abs" style="left:529px;top:2668px">Get In Touch</h5>
  <div class="abs contact-row" style="top:2714px">
    <svg width="10" height="14" viewBox="0 0 8 11"><path d="M4 0a4 4 0 00-4 4c0 3 4 7 4 7s4-4 4-7a4 4 0 00-4-4z" fill="#fff"/></svg>
    <div><strong>VENTO HALLMARK</strong><br>Lorem Ipsum is simply dummy<br>text of the printing and<br>typesetting</div>
  </div>
  <div class="abs contact-row" style="top:2806px">
    <svg width="11" height="11" viewBox="0 0 24 24"><path fill="#fff" d="M6.6 10.8a15 15 0 006.6 6.6l2.2-2.2a1 1 0 011-.25 11.4 11.4 0 003.6.57 1 1 0 011 1V20a1 1 0 01-1 1A17 17 0 013 4a1 1 0 011-1h3.5a1 1 0 011 1c0 1.25.2 2.45.57 3.57a1 1 0 01-.25 1z"/></svg>
    <div>(0987) 654 321</div>
  </div>
  <div class="abs contact-row" style="top:2844px">
    <svg width="12" height="9" viewBox="0 0 12 9"><rect width="12" height="9" fill="#fff"/><path d="M0 0l6 5 6-5" stroke="#232323" fill="none"/></svg>
    <div>info@ventohallmark.example</div>
  </div>

  <h5 class="abs" style="left:828px;top:2668px">Property Cities</h5>
  <ul class="abs cities" style="left:843px;top:2712px">
    <li>Alaska</li><li>California</li><li>colorado</li><li>Florida</li><li>Kansas</li><li>Louisiana</li><li>Michigan</li>
  </ul>
  <ul class="abs cities" style="left:962px;top:2712px">
    <li>Mississippi</li><li>New Jersey</li><li>New York</li><li>Oklahoma</li><li>Texas</li><li>Washington</li><li>Wisconsin</li>
  </ul>
</footer>

<div class="abs bottom">
  <span class="copy">© Copyright 2016, vento hallmark. All Right Reserved.</span>
  <nav><a href="#">Home</a><a class="active" href="#">About Us</a><a href="#">Costa del Sol</a><a href="#">Services</a><a href="#">Testimonials</a><a href="#">Contact Us</a></nav>
</div>

</body>
</html>
```